Psychology service brochure

Marketing brochure for a new psychological counselling service.
Our old brochure was too boring and conservative. We are selling our services to GP's, psychiatrists, other health providers and of course potential clients. We'd really like a professional, elegant look that conveys us to be compassionate and conscientious providers of psychological services.
I have included a copy of our old brochure and a copy of the changes we'd like to the text.
Updates
I have included a photo of myself and my business partner. Only the faces are needed, so backgrounds would need to be edited out.
Hello, in consultation with my business partner, we would like
the use of our photos in the brochure please (with backgrounds edited out)
no stock photos of random people
use of abstract or nature/floral motifs suggestive of tranquillity
regards,
Rosalind
Target Market(s)
General practitioner doctors, potential clients
Industry/Entity Type
Health
Requirements
Must have
- must include BlairMdITC TT- font for the business name
- must include our signature color Pantone 291 (see attached brochure)
- use of the photos of myself and my business partner (with background edited out please)
- keep use of colours to a minimum, 3 colors maximum, one of which must be Pantone 291
- must include changes to the brochure as outlined in the 'Changes to Pamphlet' document.
Nice to have
- an interesting, eye catching layout.
- interesting use of white spaces
- use of subtle abstract or nature/floral related graphics suggestive of tranquillity
Should not have
- should not include our fee
- stock photos of people

```html
<!DOCTYPE html>
<html lang="en">
<head>
<meta charset="utf-8">
<title>Quiet Harbour Counselling – Brochure</title>
<link rel="stylesheet" href="https://fonts.googleapis.com/css2?family=Arimo:ital,wght@0,400;0,700;1,400&family=Marcellus+SC&display=swap">
<style>
  :root{
    --green-deep:#0b5a14;
    --green-mid:#4fb86a;
    --green-pale:#a6dcb8;
    --aqua:#c4eef3;
    --aqua-soft:#e7f8fa;
    --paper:#ffffff;
    --stage:#eef1ee;
  }
  *{box-sizing:border-box;margin:0;padding:0}
  html,body{width:1200px;height:900px;overflow:hidden}
  body{background:var(--stage);font-family:"Arimo",Arial,sans-serif;color:var(--green-deep);position:relative}

  .sheet{position:absolute;left:30px;width:1140px;height:420px;display:flex;background:var(--paper);box-shadow:0 2px 10px rgba(0,0,0,.12)}
  .sheet--outside{top:20px}
  .sheet--inside{top:460px}
  .panel{position:relative;width:380px;height:420px;overflow:hidden;border-right:1px dashed #dfe6df}
  .panel:last-child{border-right:none}

  .edge-band{position:absolute;left:0;top:0;width:14px;height:100%;background:var(--green-deep)}
  .tab{position:absolute;background:var(--green-deep);color:var(--paper);font-weight:700;font-size:12px;letter-spacing:.04em;text-transform:uppercase;padding:8px 14px;border-radius:0 14px 14px 0;line-height:1.25}
  .body-text{position:absolute;font-size:9.5px;line-height:1.4;color:var(--green-deep)}
  .body-text p{margin-bottom:7px}
  .bullets{list-style:none}
  .bullets li{position:relative;padding-left:10px;margin-bottom:5px}
  .bullets li::before{content:"";position:absolute;left:0;top:4px;width:4px;height:4px;border-radius:50%;background:var(--green-deep)}

  /* outside: approach panel */
  .approach .tab--approach{left:14px;top:24px;width:190px}
  .approach .text--approach{left:30px;top:70px;width:320px}
  .approach .tab--clients{left:14px;top:226px;width:190px}
  .approach .text--clients{left:30px;top:272px;width:320px}

  /* outside: contact panel */
  .map-area{position:absolute;left:40px;top:40px;width:300px;height:200px;border:2px solid var(--green-deep);border-radius:10px;background:linear-gradient(135deg,var(--aqua-soft),#f4fbf5)}
  .contact{position:absolute;left:70px;top:282px;width:270px;font-size:10.5px;line-height:1.6;font-style:normal}
  .contact__venue{font-weight:700;text-transform:uppercase}
  .contact__row{display:flex}
  .contact__row span:first-child{width:56px}
  .contact__row strong{font-weight:700}

  /* cover */
  .cover-motif{position:absolute;left:0;top:0;width:300px;height:420px;background:linear-gradient(90deg,var(--green-deep) 0%,var(--green-mid) 22%,var(--green-pale) 50%,var(--aqua) 75%,var(--aqua-soft) 100%)}
  .brand-name{position:absolute;font-family:"Marcellus SC",Georgia,serif;color:var(--aqua);letter-spacing:.12em}
  .cover .brand-name{right:22px;top:30px;writing-mode:vertical-rl;font-size:22px}

  /* inside */
  .clinician-tab{position:absolute;left:14px;width:230px;background:var(--green-deep);color:var(--paper);font-size:10.5px;font-weight:700;line-height:1.35;padding:7px 12px;border-radius:0 14px 14px 0}
  .clinician-tab--first{top:14px}
  .clinician-tab--second{top:206px}
  .portrait{position:absolute;left:262px;width:96px;height:56px;border-radius:10px;background:linear-gradient(160deg,var(--aqua-soft),var(--green-pale))}
  .portrait--first{top:14px}
  .portrait--second{top:206px}
  .bio--first{left:30px;top:76px;width:330px}
  .bio--second{left:30px;top:268px;width:330px}
  .rule{position:absolute;left:0;right:24px;height:4px;background:var(--green-deep);border-radius:0 2px 2px 0}
  .rule--first{top:22px}
  .rule--second{top:214px}
  .bio--first-cont{left:24px;top:40px;width:330px}
  .bio--second-cont{left:24px;top:232px;width:330px}
  .inside-name{left:400px;bottom:16px;font-size:19px;white-space:nowrap}

  .fees{background:var(--green-deep)}
  .fees__card{position:absolute;left:34px;top:22px;right:14px;bottom:22px;background:var(--paper);border-radius:16px 0 0 16px}
  .fees .tab{left:34px;top:40px;width:200px}
  .fees .body-text{left:50px;top:86px;width:290px}
  .fees__note{position:absolute;left:50px;bottom:40px;width:290px;background:var(--green-deep);color:var(--paper);font-style:italic;font-size:9.5px;line-height:1.4;padding:12px 14px;border-radius:10px 0 10px 0}
</style>
</head>
<body>

<section class="sheet sheet--outside" aria-label="Brochure outside">
  <div class="panel approach">
    <div class="edge-band"></div>
    <h2 class="tab tab--approach">Our approach<br>to therapy</h2>
    <div class="body-text text--approach">
      <p>We are warm, compassionate and professional Clinical and General Psychologists who together have thirty years of experience and who are committed to providing high quality evidence-based treatment to our clients.</p>
      <p>Types of treatment may include Cognitive Behavioural Therapy, Motivational Interviewing and Mindfulness.</p>
      <p>We are also eligible to provide Pregnancy Support Counselling services under Medicare.</p>
    </div>
    <h2 class="tab tab--clients">What we want<br>for our clients</h2>
    <ul class="body-text text--clients bullets">
      <li>For you to feel heard and respected</li>
      <li>To have a positive experience of working collaboratively with a psychologist</li>
      <li>To connect or reconnect with feelings of hope</li>
      <li>To move beyond counselling with an understanding of your strengths and the skills to make changes that will help you to meet future challenges.</li>
    </ul>
  </div>

  <div class="panel contact-panel">
    <div class="map-area" role="img" aria-label="Street map showing the location of the centre near the train station"></div>
    <address class="contact">
      <div>Contact reception</div>
      <div class="contact__venue">The Wexley Centre</div>
      <div>18 Wexley Street, Fairmont 3090</div>
      <div class="contact__row"><span>Phone:</span><strong>9401 2765</strong></div>
      <div class="contact__row"><span>Fax:</span><strong>9401 2766</strong></div>
      <div class="contact__row"><span>Email:</span><strong>qhcounselling@example.com</strong></div>
    </address>
  </div>

  <div class="panel cover">
    <div class="cover-motif" role="img" aria-label="Abstract tranquil motif in deep green, soft green and aqua tones"></div>
    <h1 class="brand-name">Quiet Harbour Counselling</h1>
  </div>
</section>

<section class="sheet sheet--inside" aria-label="Brochure inside">
  <div class="panel clinicians">
    <div class="edge-band"></div>
    <h3 class="clinician-tab clinician-tab--first">Rosalind Harrow<br>Clinical Psychologist<br>M.Psych (Clin.) MAPS</h3>
    <div class="portrait portrait--first" role="img" aria-label="Portrait photo of Rosalind Harrow"></div>
    <div class="body-text bio--first">
      <p>Rosalind is a Clinical Psychologist with fifteen years of experience providing a range of psychological services to challenging clients within the public mental health sector including forensic, addiction and dual diagnosis services. She has been employed as a Senior Psychologist in this capacity for the last seven years.</p>
      <p>Rosalind is a trained and experienced Cognitive Behavioural Therapist and is skilled in treating individuals and groups with a range of mood disorders including anxiety, depression and panic disorder,</p>
    </div>
    <h3 class="clinician-tab clinician-tab--second">Imogen Carlisle<br>Psychologist<br>M.Psych (Clin.) MAPS</h3>
    <div class="portrait portrait--second" role="img" aria-label="Portrait photo of Imogen Carlisle"></div>
    <div class="body-text bio--second">
      <p>Imogen is a Psychologist, and with fifteen years experience working in the public health sector, seven as a Senior Psychologist, she is a highly skilled clinician in the areas of mental health, addiction and dual diagnosis.</p>
      <p>She has more recently specialised in working with adolescents but has significant experience treating adults, both individually and in a variety of group programmes. She has also facilitated numerous training events and mentored clinicians in addressing dual diagnosis issues with their clients.</p>
    </div>
  </div>

  <div class="panel clinicians-cont">
    <div class="rule rule--first"></div>
    <div class="body-text bio--first-cont">
      <p>as well as in helping clients to overcome life issues such as grief and loss, stress management and anger management.</p>
      <p>Rosalind trains other mental health clinicians and university students in treatment modalities including Motivational Interviewing and Brief Interventions. She has an interest in brain-based research into neuroplasticity and it's application to cognitive therapy and change.</p>
    </div>
    <div class="rule rule--second"></div>
    <div class="body-text bio--second-cont">
      <p>Imogen primarily utilises a Cognitive Behavioural framework and Motivational Interviewing and has a special interest in working with adolescents who are experiencing developmental difficulties, antenatal and post-natal depression/stress, and parenting issues. Additionally Imogen is skilful working in the areas of grief &amp; loss, life transition and adjustment issues, relationship and interpersonal challenges, and personal development.</p>
    </div>
  </div>

  <div class="panel fees">
    <div class="fees__card"></div>
    <h2 class="tab">Our fee structure</h2>
    <div class="body-text">
      <p>The practice accepts referrals from self-referring individuals, as well as from health professionals such as GPs, Psychiatrists, and Maternal and Child Health Nurses.</p>
      <p>Medicare rebates are available for clients referred for treatment by their GP.</p>
      <p>There are different tiers of rebates for Psychologists under Medicare, and this is dependent on treatment received (individual, group or pregnancy support counselling), and whether you are treated by a Psychologist or a Clinical Psychologist.</p>
      <p>Please contact us directly to further discuss fees for treatment.</p>
      <p>Fees are paid in full at the end of each session, and a receipt is provided which will allow you to obtain your refund at any Medicare office.</p>
    </div>
    <p class="fees__note">The practice does not bulk bill at this time, but we anticipate the addition of this facility in the future</p>
  </div>

  <div class="brand-name inside-name">Quiet Harbour Counselling</div>
</section>

</body>
</html>
```